Double-sided A5 leaflet with photos.

Design A5 leaflet double sided
With emphasis on we are cheaper than our competition as a hook
The colour can be whatever makes it look like a unique brand.
Try and use all the different photos because they are unique.
And put the different photos on there with headlines
Updates

Need extra days to review

Target Market(s)

The idea is it stands out people moving that you can offer different things to like taking their bed apart, taking their old furniture or they just want to move and want two men and the truck. Big or small or piano? Heavy furniture marble table? People who want their bed taken apart put back together again, piano moving, marble table. Moving fridge for washing machine. Moving small truck picture of big truck the poster is people walking past in the street. The pelmo leaflet is delivered to high rise unit blocks with 300 units.

Industry/Entity Type

Furniture removal

Colors
59FF00
82FF00
B8FF75
E3FFCB
F4FFEA

Requirements
Must have
• Try and use all the different photos the screenshot of the Varnex review next to the other photos we put beds together, etc
Nice to have
• It would be nice to have on one side all the different photos with headlines on each one saying what they do EG beds taken apart over the top of a photo .g

```html
<!DOCTYPE html>
<html lang="en">
<head>
<meta charset="UTF-8">
<title>Steady Haul Movers – A5 Leaflet</title>
<link rel="stylesheet" href="https://fonts.googleapis.com/css2?family=Alfa+Slab+One&family=Poppins:wght@500;600;700&display=swap">
<style>
  :root{
    --green:#1e6a2a;
    --green-dark:#145220;
    --green-deep:#0f4419;
    --yellow:#f2eb1e;
    --white:#ffffff;
    --ink:#1b1b1b;
    --page:#d4d4d4;
    --rule:#d6d6d6;
    --stamp:#e6e6e6;
  }
  *{margin:0;padding:0;box-sizing:border-box}
  html,body{width:1200px;height:2659px;overflow:hidden;background:var(--page)}
  body{position:relative;font-family:"Poppins",sans-serif;color:var(--ink)}
  .slab{font-family:"Alfa Slab One",serif;text-transform:uppercase;letter-spacing:1px;line-height:1;white-space:nowrap}

  .card{position:absolute;left:172px;width:856px;height:607px;overflow:hidden;background:var(--white);box-shadow:0 2px 6px rgba(0,0,0,.08)}
  .card--front{top:690px}
  .card--back{top:1362px}

  /* FRONT */
  .front__field{position:absolute;left:0;top:0;width:856px;height:425px;background:linear-gradient(180deg,var(--green) 0%,var(--green-dark) 100%)}
  .front__hero{position:absolute;left:30px;top:55px;width:430px;height:412px;border-radius:50% 50% 6px 6px;background:radial-gradient(circle at 45% 40%,#f1e87a 0%,#c9c247 35%,#3f8a3a 70%,var(--green-dark) 100%)}
  .brand{position:absolute;left:585px;top:40px;display:flex;align-items:center;gap:10px}
  .brand__dot{width:34px;height:34px;border-radius:50%;background:var(--yellow)}
  .brand__name{font-family:"Alfa Slab One",serif;color:var(--white);font-size:22px;line-height:1.05;text-transform:uppercase}
  .front__headline{position:absolute;left:478px;top:200px}
  .front__headline .line{display:block;font-size:44px;color:var(--yellow);margin-bottom:4px}
  .front__headline .line--big{font-size:64px;color:var(--white);margin-top:6px}
  .contact-bar{position:absolute;left:320px;top:425px;width:536px;height:46px;background:var(--yellow);clip-path:polygon(18px 0,100% 0,100% 100%,0 100%);display:flex;align-items:center;padding-left:30px;gap:12px;white-space:nowrap}
  .contact-bar__phone{font-family:"Alfa Slab One",serif;color:var(--green);font-size:27px;line-height:1}
  .contact-bar__rule{width:2px;height:26px;background:var(--green);flex:none}
  .contact-bar__web{font-family:"Alfa Slab One",serif;color:var(--green);font-size:12px;letter-spacing:.3px;line-height:1}

  .compare{position:absolute;left:0;top:478px;width:856px;height:129px;display:flex}
  .compare__col{position:relative;height:100%}
  .compare__col + .compare__col::before{content:"";position:absolute;left:0;top:16px;bottom:14px;width:2px;background:var(--rule)}
  .compare__col--a{width:293px}
  .compare__col--b{width:274px}
  .compare__col--c{width:289px}
  .rival{position:absolute;display:flex;align-items:center;gap:8px;font-weight:700;font-size:15px;color:var(--ink);line-height:1.1}
  .rival__mark{width:44px;height:44px;border-radius:50%;background:var(--green);flex:none}
  .rival__mark--sq{border-radius:0;width:26px;height:26px;background:var(--ink)}
  .price{position:absolute;background:var(--green);color:var(--yellow);font-weight:700;font-size:20px;width:76px;height:30px;display:flex;align-items:center;justify-content:center}
  .price sup{font-size:10px;margin-right:2px;color:var(--white)}
  .note{position:absolute;font-size:12px;font-weight:500;line-height:1.25;color:var(--ink);white-space:nowrap}

  /* BACK */
  .back__shape{position:absolute;left:0;top:0}
  .back__headline{position:absolute;left:42px;top:68px}
  .back__headline .line{display:block;font-size:36px;color:var(--yellow)}
  .back__headline .line--white{color:var(--white);margin-top:4px}
  .photo{position:absolute;border:4px solid var(--yellow);background:linear-gradient(160deg,#d9d4c8 0%,#a89a82 55%,#6f6450 100%)}
  .photo--one{left:40px;top:200px;width:142px;height:215px;transform:skewY(-4deg)}
  .photo--two{left:186px;top:178px;width:142px;height:210px;transform:skewY(-4deg);background:linear-gradient(160deg,#eeeeea 0%,#b8a98d 60%,#7a5a38 100%)}
  .photo--three{left:328px;top:170px;width:118px;height:232px;transform:skewY(-4deg);background:linear-gradient(160deg,#e8e4da 0%,#8a5a2e 50%,#5a3a1c 100%)}
  .back__truck{position:absolute;left:368px;top:350px;width:180px;height:225px;border-radius:8px;background:linear-gradient(170deg,#3b8a8c 0%,#f2f2f2 55%,#cfcfcf 100%)}
  .call-tag{position:absolute;left:42px;top:440px;height:24px;padding:0 14px;background:linear-gradient(90deg,#8bc34a,var(--green));clip-path:polygon(8px 0,100% 0,calc(100% - 8px) 100%,0 100%);display:flex;align-items:center;font-family:"Alfa Slab One",serif;color:var(--white);font-size:12px;letter-spacing:.5px}
  .back__phone{position:absolute;left:42px;top:474px;font-family:"Alfa Slab One",serif;color:var(--yellow);font-size:39px;line-height:1;white-space:nowrap}
  .back__web{position:absolute;left:44px;top:528px;font-family:"Alfa Slab One",serif;color:var(--white);font-size:13px;letter-spacing:.3px;white-space:nowrap}
  .stamp{position:absolute;left:725px;top:35px;width:95px;height:95px;background:var(--stamp)}
  .address-line{position:absolute;left:568px;width:252px;height:2px;background:var(--rule)}
</style>
</head>
<body>

<section class="card card--front" aria-label="Leaflet front">
  <div class="front__field"></div>
  <div class="front__hero" role="img" aria-label="Illustrated mover in yellow uniform holding a fragile box in front of a removal truck"></div>

  <div class="brand">
    <span class="brand__dot"></span>
    <span class="brand__name">Steady Haul<br>Movers</span>
  </div>

  <h1 class="front__headline slab">
    <span class="line">Very Very</span>
    <span class="line">Very Cheap</span>
    <span class="line line--big">Movers</span>
  </h1>

  <div class="contact-bar">
    <span class="contact-bar__phone">0400 555 222</span>
    <span class="contact-bar__rule"></span>
    <span class="contact-bar__web">WWW.STEADYHAULMOVERS.COM.AU</span>
  </div>

  <div class="compare">
    <div class="compare__col compare__col--a">
      <div class="rival" style="left:40px;top:34px;width:140px"><span class="rival__mark rival__mark--sq"></span><span>Dual Crew<br>Trucks</span></div>
      <span class="note" style="left:187px;top:4px;font-size:11px">1<sup>st</sup> Hour</span>
      <div class="price" style="left:187px;top:22px"><sup>$</sup>465</div>
      <span class="note" style="left:187px;top:57px">Then Per Hour</span>
      <div class="price" style="left:187px;top:76px"><sup>$</sup>250</div>
    </div>
    <div class="compare__col compare__col--b">
      <div class="rival" style="left:28px;top:34px;width:130px"><span class="rival__mark"></span><span>Solo<br>Van Co</span></div>
      <div class="price" style="left:167px;top:22px"><sup>$</sup>225</div>
      <span class="note" style="left:167px;top:58px">Per Hour Base<br>to Base From<br>Eastvale</span>
    </div>
    <div class="compare__col compare__col--c">
      <div class="rival" style="left:30px;top:34px;width:140px"><span class="rival__mark"></span><span>Steady<br>Haul</span></div>
      <div class="price" style="left:168px;top:22px"><sup>$</sup>170</div>
      <span class="note" style="left:168px;top:58px">Per Hour no<br>base to base<br>change</span>
    </div>
  </div>
</section>

<section class="card card--back" aria-label="Leaflet back">
  <svg class="back__shape" width="856" height="607" viewBox="0 0 856 607" aria-hidden="true">
    <path d="M0 0 H345 C520 40 590 330 545 607 H0 Z" fill="var(--yellow)"/>
    <path d="M0 0 H330 C480 50 535 330 497 607 H0 Z" fill="var(--green)"/>
  </svg>

  <h2 class="back__headline slab">
    <span class="line">Very Very Very</span>
    <span class="line line--white">Cheap Movers</span>
  </h2>

  <div class="photo photo--one" role="img" aria-label="Photo of a mover assembling a timber bed frame on the floor"></div>
  <div class="photo photo--two" role="img" aria-label="Photo of a mover putting together a white bed frame in a bedroom"></div>
  <div class="photo photo--three" role="img" aria-label="Photo of a mover beside a large carved wooden wardrobe wrapped for transport"></div>
  <div class="back__truck" role="img" aria-label="Illustrated removal truck with branded box body"></div>

  <div class="call-tag">CALL DIRECT</div>
  <div class="back__phone">0400 555 222</div>
  <div class="back__web">WWW.STEADYHAULMOVERS.COM.AU</div>

  <div class="stamp" aria-hidden="true"></div>
  <div class="address-line" style="top:190px"></div>
  <div class="address-line" style="top:245px"></div>
  <div class="address-line" style="top:300px"></div>
</section>

</body>
</html>
```